Life Coaching business needs a new flyer

We are an Australian business that specialises in Life Coaching, Career Coaching, Health and Wellness Coaching, Yoga and Pilates. We need a A4 double sided flyer that is full colour and folded to DL format. I have attached a couple of designs that I like and some pictures and would like the flyer to be bright yet stylish.

Industry/Entity Type

Life Coaching

```html
<!DOCTYPE html>
<html lang="en">
<head>
<meta charset="utf-8">
<title>Clearpath Coaching – Inside Spread</title>
<link href="https://fonts.googleapis.com/css2?family=Open+Sans:wght@600;700&family=Raleway:wght@400;500&display=swap" rel="stylesheet">
<style>
  :root {
    --page-bg: #ece9e4;
    --paper: #ffffff;
    --heading-blue: #2b8fd3;
    --question-navy: #1c3668;
    --body-ink: #2a2a2a;
    --bullet-blue: #2b8fd3;
    --brand-green: #5aa63a;
    --sea-light: #7fd6dc;
    --sea-deep: #2ba2b6;
    --sky-blue: #3a9fdc;
    --sky-pale: #bfe3f6;
    --studio-white: #eef0f1;
    --warm-skin: #d9a882;
    --deck-white: #d8dde0;
    --sunlit: #e9c27a;
    --greenery: #8fb46a;
  }
  * { box-sizing: border-box; margin: 0; padding: 0; }
  html, body { width: 1200px; height: 1000px; overflow: hidden; }
  body { background: var(--page-bg); font-family: "Raleway", sans-serif; color: var(--body-ink); position: relative; }

  .spread { position: absolute; left: 72px; top: 45px; width: 1068px; height: 823px; background: var(--paper); overflow: hidden; }
  .photo, .block { position: absolute; }

  h2 { font-family: "Open Sans", sans-serif; font-weight: 600; color: var(--heading-blue); font-size: 16px; line-height: 1.2; margin-bottom: 4px; }
  p { font-size: 12px; line-height: 1.28; margin-bottom: 12px; }

  /* panel 1 */
  .photo--sea { left: 0; top: 0; width: 354px; height: 398px; background: linear-gradient(160deg, var(--sea-light) 0%, #a8e6df 35%, var(--sea-deep) 100%); }
  .questions { left: 16px; top: 28px; width: 200px; font-family: "Open Sans", sans-serif; font-weight: 700; font-size: 15.5px; line-height: 1.28; color: var(--question-navy); }
  .questions li { list-style: none; margin-bottom: 18px; }
  .photo--team { left: 0; top: 398px; width: 354px; height: 197px; background: linear-gradient(180deg, #ffffff 0%, var(--studio-white) 60%, #dfe5ea 100%); }
  .about { left: 19px; top: 610px; width: 320px; }
  .about p { margin-bottom: 14px; }

  /* panel 2 */
  .life { left: 372px; top: 24px; width: 330px; }
  .photo--couple { left: 354px; top: 183px; width: 354px; height: 215px; background: linear-gradient(90deg, var(--warm-skin) 0%, #c8d8de 45%, var(--deck-white) 70%, #e79a52 100%); }
  .career { left: 372px; top: 407px; width: 330px; }
  .wellness { left: 372px; top: 554px; width: 330px; }
  .photo--yoga { left: 354px; top: 643px; width: 354px; height: 180px; background: linear-gradient(180deg, var(--sky-blue) 0%, var(--sky-pale) 70%, #f4f6f7 72%, #ffffff 100%); }

  /* panel 3 */
  .help { left: 728px; top: 24px; width: 320px; }
  .help-list { list-style: none; margin-left: 20px; margin-top: -2px; }
  .help-list li { position: relative; padding-left: 12px; font-size: 13px; line-height: 1.25; margin-bottom: 4px; width: 240px; }
  .help-list li::before { content: ""; position: absolute; left: 0; top: 5px; width: 6px; height: 6px; background: var(--bullet-blue); }
  .meditation { left: 728px; top: 325px; width: 320px; }
  .yoga { left: 728px; top: 421px; width: 320px; }
  .brand { left: 735px; top: 555px; width: 310px; display: flex; align-items: center; gap: 12px; }
  .brand-mark { width: 58px; height: 58px; border-radius: 50%; background: var(--brand-green); flex: none; }
  .brand-name { font-family: "Raleway", sans-serif; font-weight: 500; font-size: 17px; line-height: 1.15; color: var(--brand-green); }
  .photo--joy { left: 708px; top: 643px; width: 119px; height: 180px; background: linear-gradient(180deg, #9fd3ea 0%, #e8b8c8 60%, #d46a8e 100%); }
  .photo--meal { left: 828px; top: 643px; width: 119px; height: 180px; background: linear-gradient(180deg, #efefe9 0%, #e6a5b6 60%, #c98aa0 100%); }
  .photo--family { left: 948px; top: 643px; width: 120px; height: 180px; background: linear-gradient(160deg, var(--sunlit) 0%, var(--greenery) 100%); }
</style>
</head>
<body>
<main class="spread">
  <!-- panel 1 -->
  <div class="photo photo--sea" role="img" aria-label="Woman floating on a pink lilo in clear turquoise water"></div>
  <ul class="block questions">
    <li>Are you looking at making changes this year?</li>
    <li>Are you stuck in a rut or at a crossroad in your life?</li>
    <li>Are you wanting to lose weigh but can’t get motivated?</li>
    <li>Do you have ongoing problems with your career, relationships, or just life itself?</li>
    <li>Life coaching is the answer</li>
  </ul>
  <div class="photo photo--team" role="img" aria-label="Group of smiling, celebrating people on a white background"></div>
  <section class="block about">
    <h2>Clearpath Coaching and Meditation Centre</h2>
    <p>Our mission is to help you become the best possible person you can be. Mentally, physically, and spiritually.</p>
    <p>We offer highly qualified and compassionate trainers/coaches for Life Coaching, Meditation, Yoga and Pilates.<br>They will guide and motivate you every step of the way to achieve all your dreams and goals.</p>
    <p>They will make you be the best you can be J</p>
  </section>

  <!-- panel 2 -->
  <section class="block life">
    <h2>Life Coaching</h2>
    <p>Your Life Coach will give you the confidence and the ability to move forward in a positive manner in all areas of your life where you crave change.</p>
    <p>Life Coaching is about breaking down the barriers preventing this change from happening, and creating the ideal environment for positive action to take place. It is a holistic approach, which looks at the present and sets goals for a totally successful future.</p>
  </section>
  <div class="photo photo--couple" role="img" aria-label="Smiling older couple sharing champagne on a boat deck by the sea"></div>
  <section class="block career">
    <h2>Career Coaching</h2>
    <p>Are you at a crossroads in your career and at a loss about what to do next? Do you want your work to be in alignment with the authentic you? It can be difficult to assess career options, goals, and strategies, and have the confidence to implement changes on your own. With the right coaching support, you will gain the clarity that you need to take control and have a fulfilling and rewarding career.</p>
  </section>
  <section class="block wellness">
    <h2>Wellness Coaching</h2>
    <p>Health and wellness coaches help their clients find the motivation and tools to achieve their health and wellness goals, working with the client to examine and improve the psychological framework that supports those goals.</p>
  </section>
  <div class="photo photo--yoga" role="img" aria-label="Woman in white doing a yoga balance pose against a blue sky"></div>

  <!-- panel 3 -->
  <section class="block help">
    <h2>Why Would I Need Help?</h2>
    <p>Coaching is for anyone who wants to make lasting changes in their life. Coaching can assist with such issues as:</p>
    <ul class="help-list">
      <li>Creating a better work- life balance</li>
      <li>Resolving relationship issues</li>
      <li>Career guidance</li>
      <li>Stress management</li>
      <li>Weight loss and fitness</li>
      <li>Motivation and goal setting</li>
      <li>Boosting your self esteem</li>
      <li>Overcoming negative emotions and thoughts</li>
      <li>Better time management</li>
    </ul>
  </section>
  <section class="block meditation">
    <h2>Meditation</h2>
    <p>We specialise in teaching meditation from beginners to advanced and teach a variety of techniques for stress reduction, peace of mind, stillness, and clarity.</p>
  </section>
  <section class="block yoga">
    <h2>Yoga/Pilates</h2>
    <p>Your highly qualified and experienced Yoga or Pilates instructor will come to you and create a fun and varied workout based on what you enjoy and what your goals are.</p>
  </section>
  <div class="block brand">
    <span class="brand-mark" aria-hidden="true"></span>
    <span class="brand-name">Clearpath Coaching and Meditation Centre</span>
  </div>
  <div class="photo photo--joy" role="img" aria-label="Joyful woman in a floral dress with arms raised beside a pink car"></div>
  <div class="photo photo--meal" role="img" aria-label="Smiling man in a pink shirt eating a bowl of salad"></div>
  <div class="photo photo--family" role="img" aria-label="Mother carrying her daughter piggyback in a sunny park"></div>
</main>
</body>
</html>
```